Fresh, modern, fun business card for pediatric dental practice

Need a business card for fresh, modern, fun pediatric dental practice

Clean look that matches our website's font and colors

We prefer the look of curved corners on business cards

Target Market(s)

parents (mothers) of young children, professionals, mid-high class

Industry/Entity Type

Dental

Contact Information for Business Card

Maplebrook Pediatric Dentistry
482 Quarry Lane
Suite 517
Alder Falls, PA 17560
717.555.0193
www.maplebrookkidsdental.example

Mei-Ran Tsai, DMD
Corinne Walbeck, DMD
(we are working on our email address, but we would like that on the card as well)

Font styles to use
Sans Serif

Requirements
Must have
• All info; we would also like to make cards for individual staff members
• colors from our website and color palatte, attatched
• use same font and design as website for branding
Nice to have
• clean, simple card that has a pop of color
• we would like to see a few designs with our tag line "where happy smiles grow"
• we are not sure if we want to have it on there or not
• we would like to see a few designs incorporating the ribbon graphic on our website where the word WELCOME is

```html
<!DOCTYPE html>
<html lang="en">
<head>
<meta charset="utf-8">
<title>Maplebrook Pediatric Dentistry – Business Card</title>
<link rel="stylesheet" href="https://fonts.googleapis.com/css2?family=Open+Sans:wght@400;600&family=Roboto:ital,wght@0,400;1,500&family=Roboto+Condensed:wght@500&display=swap">
<style>
  :root {
    --stage: #2a2a2a;
    --magenta: #d4338f;
    --sun: #f9b823;
    --sun-soft: #fde7b0;
    --paper: #f4f4f2;
    --ink: #4a4a4a;
    --white: #ffffff;
  }
  * { margin: 0; padding: 0; box-sizing: border-box; }
  html, body { width: 1200px; height: 960px; overflow: hidden; }
  body { background: var(--stage); position: relative; font-family: "Roboto", Arial, sans-serif; }

  .card { position: absolute; width: 598px; height: 342px; border-radius: 22px; overflow: hidden; }

  /* front */
  .card--front { left: 322px; top: 108px; background: var(--magenta); }
  .front-mark { position: absolute; left: 50%; top: 90px; width: 56px; height: 56px; margin-left: -28px; border-radius: 50%; background: var(--sun); }
  .front-name { position: absolute; left: 0; right: 0; top: 170px; text-align: center; font-family: "Open Sans", Arial, sans-serif; }
  .front-name__main { display: block; color: var(--sun); font-weight: 600; font-size: 50px; line-height: 1; letter-spacing: 1px; }
  .front-name__sub { display: block; color: var(--white); font-weight: 400; font-size: 26px; line-height: 1.3; letter-spacing: 1.5px; margin-top: 2px; }

  /* back */
  .card--back { left: 320px; top: 493px; background: var(--paper); }
  .back-name { position: absolute; left: 28px; top: 18px; font-family: "Open Sans", Arial, sans-serif; }
  .back-name__main { display: block; color: var(--sun); font-weight: 600; font-size: 40px; line-height: 1.05; letter-spacing: 1px; }
  .back-name__sub { display: block; color: var(--magenta); font-weight: 400; font-size: 20px; line-height: 1.2; letter-spacing: 1.2px; }
  .doctors { position: absolute; left: 28px; top: 101px; color: var(--sun); font-family: "Roboto Condensed", Arial, sans-serif; font-weight: 500; font-size: 20px; line-height: 23px; text-transform: uppercase; }
  .address { position: absolute; left: 28px; top: 153px; color: var(--ink); font-size: 14.5px; line-height: 18px; }
  .contact { position: absolute; left: 28px; top: 215px; list-style: none; color: var(--ink); font-size: 14.5px; line-height: 19.5px; }
  .contact li { display: flex; align-items: center; gap: 7px; }
  .contact svg { width: 13px; height: 13px; fill: var(--sun); flex: none; }
  .tagline { position: absolute; left: 0; top: 285px; width: 258px; height: 35px; }
  .tagline svg { position: absolute; inset: 0; }
  .tagline__text { position: absolute; left: 31px; top: 8px; color: var(--white); font-style: italic; font-weight: 500; font-size: 15px; }
  .emblem { position: absolute; left: 305px; top: 40px; width: 250px; height: 250px; border-radius: 50%; background: radial-gradient(circle, var(--sun-soft) 0%, #fbd370 70%, var(--sun) 100%); opacity: .85; }
</style>
</head>
<body>

<section class="card card--front">
  <div class="front-mark"></div>
  <div class="front-name">
    <span class="front-name__main">maplebrook</span>
    <span class="front-name__sub">pediatric dentistry</span>
  </div>
</section>

<section class="card card--back">
  <div class="back-name">
    <span class="back-name__main">maplebrook</span>
    <span class="back-name__sub">pediatric dentistry</span>
  </div>
  <p class="doctors">Mei-Ran Tsai, DMD<br>Corinne Walbeck, DMD</p>
  <p class="address">Maplebrook Pediatric Dentistry<br>482 Quarry Lane, Suite 517<br>Alder Falls, PA 17560</p>
  <ul class="contact">
    <li><svg viewBox="0 0 24 24"><path d="M6.6 10.8a15 15 0 0 0 6.6 6.6l2.2-2.2c.3-.3.7-.4 1-.2 1.1.4 2.3.6 3.6.6.6 0 1 .4 1 1V20c0 .6-.4 1-1 1A17 17 0 0 1 3 4c0-.6.4-1 1-1h3.5c.6 0 1 .4 1 1 0 1.3.2 2.5.6 3.6.1.3 0 .7-.2 1z"/></svg>717.555.0193</li>
    <li><svg viewBox="0 0 24 24"><path d="M2 5h20v14H2z"/></svg>info@maplebrookkidsdental.example</li>
    <li><svg viewBox="0 0 24 24"><circle cx="12" cy="12" r="10"/></svg>maplebrookkidsdental.example</li>
  </ul>
  <div class="tagline">
    <svg viewBox="0 0 258 35" width="258" height="35"><polygon points="0,0 258,0 240,17.5 258,35 0,35" fill="var(--magenta)"/></svg>
    <span class="tagline__text">where happy smiles grow</span>
  </div>
  <div class="emblem" role="img" aria-label="Large practice emblem area in warm yellow"></div>
</section>

</body>
</html>
```